Psychiatric Office Needs a Website- 1st Time Ever!

Been in practice since 2003 with no website, but finally ready to dive in. We are Maplecrest Behavioral Healthcare, a mental health outpatient practice based in Fayetteville, Georgia that sees diverse individuals and families from childhood to advanced age for a variety of conditions. We've grown by word of mouth and referral but would now like to have a digital footprint. Be the pioneer of our website and we will be sure to share. We would like to see designs that are modern, animated, fairly colorful, easy to read, and caters to all ages. Also, we would like the design to take the whole page (not be centered) and can be viewed well on phone/tablet. Please see our outline for more information. Our motto/slogan is: Maplecrest Behavioral Healthcare- A step forward in your wellness journey, so the design should try to reflect that.
Updates

Project Deadline Extended
Reason: site in progress

Target Market(s)

Children through elderly

Industry/Entity Type

Medical

Logo Text

Stepping forward in your wellness journey

Number of Pages Required

1 page

Colors

Designer to choose colors to be used in the design.

Requirements
Must have
• Animation or moving pictures.
• Color.
• Concise.
• User friendly
• Diversity in the stock photos

```html
<!DOCTYPE html>
<html lang="en">
<head>
<meta charset="utf-8">
<title>Maplecrest Behavioral Healthcare</title>
<link href="https://fonts.googleapis.com/css2?family=Open+Sans:wght@400;600;700&display=swap" rel="stylesheet">
<style>
:root{
  --brand:#2a5591;
  --brand-dark:#234a80;
  --ink:#222;
  --muted:#666;
  --line:#dcdcdc;
  --panel:#f1f1f1;
  --foot:#e9e9e9;
  --foot-dark:#333;
  --white:#fff;
}
*{box-sizing:border-box;margin:0;padding:0}
html,body{width:1200px;height:3297px;overflow:hidden}
body{font-family:'Open Sans',sans-serif;color:var(--ink);background:var(--white);position:relative}
.abs{position:absolute}
.btn{display:inline-flex;align-items:center;justify-content:center;border:2px solid var(--line);background:var(--white);color:var(--muted);font-size:11px}
/* header */
.header{height:176px}
.brand{left:127px;top:26px;display:flex;align-items:center;gap:14px}
.brand-dot{width:56px;height:56px;border-radius:50%;background:var(--brand)}
.brand-name{font-size:20px;font-weight:700;color:var(--brand);width:230px;line-height:1.25}
.info{top:46px;font-size:11px;color:var(--muted);text-align:right;line-height:1.5}
.icon-ring{width:30px;height:30px;border:2px solid var(--line);border-radius:50%;display:flex;align-items:center;justify-content:center}
.topbtn{top:48px;height:34px;gap:7px;font-size:12px;padding:0 12px}
.nav{right:132px;top:140px;display:flex;gap:32px;font-size:13px;font-weight:600;color:var(--brand-dark)}
.nav .active{color:#4a7ac0}
/* hero */
.hero{top:176px;left:0;width:1200px;height:437px;background:linear-gradient(90deg,#d8dde3 0%,#eceef0 45%,#d9c7b8 75%,#c9b6a4 100%)}
.hero-kicker{left:308px;top:296px;font-size:21px;color:#333}
.hero-title{left:308px;top:322px;font-size:31px;font-weight:700;color:var(--brand);line-height:1.25}
.arrow{top:380px;width:26px;height:26px;border-radius:50%;background:rgba(90,90,90,.6);display:flex;align-items:center;justify-content:center}
/* welcome */
.welcome h2{position:absolute;top:686px;width:1200px;text-align:center;font-size:31px;color:var(--brand);font-weight:600}
.welcome p{position:absolute;top:732px;left:140px;width:920px;text-align:center;font-size:15.5px;line-height:1.6}
/* services */
.services{left:132px;top:912px;width:936px;height:499px;background:var(--panel)}
.tab{top:0;height:58px;width:468px;display:flex;align-items:center;justify-content:center;font-size:17px}
.tab.current{left:0;background:var(--brand);color:var(--white)}
.tab.prospect{left:468px;background:#e6e6e6;color:var(--muted);border-bottom:4px solid var(--brand)}
.svc-list{left:40px;top:110px;list-style:none}
.svc-list li{height:56px;font-size:14px;color:#444;display:flex;align-items:flex-start;gap:14px}
.svc-list li::before{content:"";border-left:6px solid #555;border-top:4px solid transparent;border-bottom:4px solid transparent;margin-top:6px}
.svc-list li.on{color:var(--brand)}
.svc-list li.on::before{border-left-color:var(--brand)}
.svc-card{left:483px;top:77px;width:436px;height:409px;background:var(--white)}
.svc-photo{height:200px;background:linear-gradient(90deg,#9aa4ae,#c8bfb2 55%,#6b6f78)}
.svc-card h3{margin:24px 20px 12px;font-size:19px;font-weight:400;color:var(--brand)}
.svc-card p{margin:0 20px;font-size:10.5px;line-height:1.55;color:var(--muted)}
/* conditions */
.conditions{top:1495px;left:0;width:1200px;height:960px;background:var(--brand)}
.conditions h2{position:absolute;top:54px;width:1200px;text-align:center;color:var(--white);font-size:31px;font-weight:600}
.cond{width:299px;background:var(--white)}
.cond .ph{height:191px}
.cond h3{margin:20px 15px 10px;font-size:15px;color:var(--brand);font-weight:600;line-height:1.35}
.cond p{margin:0 15px;font-size:11px;color:#555;line-height:1.55;height:62px}
.cond .more{margin:0 15px;width:94px;height:34px;background:#e4e4e4;color:#555;font-size:10px;display:flex;align-items:center;justify-content:center}
/* faq */
.faq h2{position:absolute;top:2524px;width:1200px;text-align:center;font-size:31px;color:var(--brand);font-weight:600}
.faq .q{position:absolute;top:2578px;width:1200px;text-align:center;font-size:19px}
.faq .a{position:absolute;top:2609px;width:1200px;text-align:center;font-size:13px}
.rule{top:2763px;left:0;width:1200px;height:1px;background:#e3e3e3}
/* news */
.news-title{top:2832px;width:1200px;display:flex;justify-content:center;align-items:center;gap:36px;font-size:31px;color:var(--brand);font-weight:600}
.sq{width:24px;height:24px;border:2px solid var(--line);display:flex;align-items:center;justify-content:center}
.news{top:2897px;width:217px;height:127px;background:#f0f0f0;padding:20px 18px}
.news p{font-size:15px;line-height:1.35}
.news time{display:block;margin-top:8px;font-size:11px;color:var(--muted)}
/* footer */
.foot{top:3099px;left:0;width:1200px;height:92px;background:var(--foot);font-size:12px;color:#444}
.foot span{position:absolute;top:38px;display:flex;align-items:center;gap:8px}
.foot-dark{top:3191px;left:0;width:1200px;height:106px;background:var(--foot-dark);color:#bbb;font-size:11px}
.foot-links{left:132px;top:32px}
.copy{left:132px;top:58px}
.social{left:1040px;top:44px;width:26px;height:26px;border-radius:50%;background:#2a7ab8}
</style>
</head>
<body>
<header class="header">
  <div class="abs brand"><div class="brand-dot"></div><div class="brand-name">Maplecrest Behavioral Healthcare</div></div>
  <div class="abs info" style="left:470px">Mon - Fri : 9AM to 6PM<br>Sat - Sun : 9AM to 1 PM</div>
  <div class="abs icon-ring" style="left:612px;top:48px"><svg width="14" height="14" viewBox="0 0 14 14"><circle cx="7" cy="7" r="6" fill="none" stroke="#888" stroke-width="1.5"/><path d="M7 3v4h3" fill="none" stroke="#888" stroke-width="1.5"/></svg></div>
  <div class="abs info" style="left:690px">Phone<br>470 555 0182</div>
  <div class="abs icon-ring" style="left:748px;top:48px"><svg width="14" height="14" viewBox="0 0 14 14"><path d="M3 1l3 3-2 2c1 2 2 3 4 4l2-2 3 3-2 2C6 13 1 8 1 3z" fill="#888"/></svg></div>
  <div class="abs btn topbtn" style="left:802px;width:120px">&#10140; Patient Portal</div>
  <div class="abs btn topbtn" style="left:931px;width:137px">&#9998; Take a Screening</div>
  <nav class="abs nav"><span class="active">HOME</span><span>ABOUT US</span><span>SERVICES</span><span>CONDITIONS WE TREAT</span><span>NEW PATIENTS</span><span>CONTACT US</span></nav>
</header>

<section class="abs hero" role="img" aria-label="Photo of a counsellor talking with a client in a bright office"></section>
<div class="abs hero-kicker">Maplecrest Behavioral Healthcare</div>
<div class="abs hero-title">A STEP FORWARD IN YOUR<br>WELLNESS JOURNEY</div>
<div class="abs arrow" style="left:33px"><svg width="10" height="10"><path d="M7 1L3 5l4 4" stroke="#fff" stroke-width="2" fill="none"/></svg></div>
<div class="abs arrow" style="left:1140px"><svg width="10" height="10"><path d="M3 1l4 4-4 4" stroke="#fff" stroke-width="2" fill="none"/></svg></div>

<section class="welcome">
  <h2>WELCOME TO MBHC</h2>
  <p>To be the leading provider of outpatient psychiatric care in Atlanta Metro South, working together to promote (the) mental wellness of our community.</p>
  <div class="abs btn" style="left:552px;top:796px;width:96px;height:37px">Read more</div>
</section>

<section class="abs services">
  <div class="abs tab current">SERVICES - (CURRENT)</div>
  <div class="abs tab prospect">SERVICES - (PROSPECTIVE)</div>
  <ul class="abs svc-list">
    <li class="on">Diagnostic evaluation and treatment</li>
    <li>Psychopharmacology</li>
    <li>Bariatric pre-surgical consultation (and other surgeries)</li>
    <li>Disability and work-related reports (Include?)</li>
    <li>Early childhood Assessments</li>
    <li>Substance abuse assessments</li>
    <li>Developmental disabilities</li>
  </ul>
  <div class="abs svc-card">
    <div class="svc-photo" role="img" aria-label="Photo of a patient in conversation with a psychiatrist"></div>
    <h3>Diagnostic evaluation and treatment</h3>
    <p>Our clinicians begin with a careful evaluation of your history, symptoms and goals. Together we build a clear treatment plan, review progress at each visit and adjust care as your needs change over time, so you always know the next step forward.</p>
    <div class="btn" style="margin:18px 20px 0;width:96px;height:37px">Read more</div>
  </div>
</section>

<section class="abs conditions">
  <h2>CONDITIONS WE TREAT</h2>
  <div class="abs cond" style="left:132px;top:121px;height:382px"><div class="ph" role="img" aria-label="Photo of a woman showing shifting moods" style="background:linear-gradient(90deg,#c9ccd0,#e7e7e8,#b9998a)"></div><h3>MOOD DISORDERS</h3><p>Depression, Bipolar, Seasonal Affective Disorder, Cyclothymic Disorder, Premenstrual Dysphoric Disorder, Disruptive Mood Dysregulation Disorder</p><div class="more">READ MORE</div></div>
  <div class="abs cond" style="left:451px;top:121px;height:382px"><div class="ph" role="img" aria-label="Photo of an anxious man holding his head" style="background:linear-gradient(180deg,#bfc2b8,#8c8f88)"></div><h3>ANXIETY DISORDERS</h3><p>Generalized Anxiety, Panic, PTSD, OCD</p><div class="more">READ MORE</div></div>
  <div class="abs cond" style="left:769px;top:121px;height:382px"><div class="ph" role="img" aria-label="Photo of a child sitting alone by a window" style="background:linear-gradient(90deg,#5d6670,#b5bcc0,#8a9a8c)"></div><h3>COMMON DISORDERS OF CHILDHOOD</h3><p style="height:42px">ADHD, Oppositional Defiant Disorder</p><div class="more">READ MORE</div></div>
  <div class="abs cond" style="left:132px;top:527px;height:367px"><div class="ph" role="img" aria-label="Photo of a sleepless woman beside an alarm clock" style="background:linear-gradient(90deg,#2d4058,#6f8aa8,#9fb4c8)"></div><h3>SLEEP ISSUES</h3><p>Insomnia, restless nights and broken sleep can affect mood and health. We help find causes and build routines that restore rest.</p><div class="more">READ MORE</div></div>
  <div class="abs cond" style="left:451px;top:527px;height:367px"><div class="ph" role="img" aria-label="Photo of a blurred woman suggesting psychosis" style="background:linear-gradient(90deg,#9fb8c0,#d9d2c0,#a8bec4)"></div><h3>PSYCHOTIC DISORDERS</h3><p>Schizophrenia, Brief Psychotic Episodes</p><div class="more">READ MORE</div></div>
  <div class="abs cond" style="left:769px;top:527px;height:367px"><div class="ph" role="img" aria-label="Photo of a man at an open refrigerator at night" style="background:linear-gradient(90deg,#2a2520,#8a6a3c,#3a342c)"></div><h3>ADDICTION, EATING DISORDERS</h3><p>Support for substance use and eating concerns, with steady care aimed at lasting recovery.</p><div class="more">READ MORE</div></div>
</section>

<section class="faq">
  <h2>FAQ</h2>
  <div class="q">What do I need to bring with me to my first visit?</div>
  <div class="a">Insurance card, patient forms found on our Form's page.</div>
  <div class="abs btn" style="left:552px;top:2642px;width:96px;height:39px">View All</div>
</section>
<div class="abs rule"></div>

<div class="abs news-title"><span class="sq"><svg width="8" height="10"><path d="M6 1L2 5l4 4" stroke="#999" stroke-width="1.5" fill="none"/></svg></span>LATEST NEWS<span class="sq"><svg width="8" height="10"><path d="M2 1l4 4-4 4" stroke="#999" stroke-width="1.5" fill="none"/></svg></span></div>
<article class="abs news" style="left:132px"><p>New evening hours now open for new patients.</p><time>20 Sep, 2017</time></article>
<article class="abs news" style="left:371px"><p>Tips for easing back-to-school stress at home.</p><time>20 Sep, 2017</time></article>
<article class="abs news" style="left:610px"><p>Meet the newest member of our care team.</p><time>20 Sep, 2017</time></article>
<article class="abs news" style="left:851px"><p>Online screening forms are now available.</p><time>20 Sep, 2017</time></article>

<footer>
  <div class="abs foot">
    <span style="left:132px">&#9679; 118 Redbud Lane, Fayetteville, GA 30214</span>
    <span style="left:468px">&#9742; 470 555 0147</span>
    <span style="left:634px">&#9113; 470 555 0193</span>
    <span style="left:820px">&#9993; info@maplecrestbehavioral.com</span>
  </div>
  <div class="abs foot-dark">
    <div class="abs foot-links">Home &nbsp;|&nbsp; About Us &nbsp;|&nbsp; Services &nbsp;|&nbsp; Conditions We Treat &nbsp;|&nbsp; New Patients &nbsp;|&nbsp; Contact Us</div>
    <div class="abs copy">Copyright &copy; 2017 Maplecrest Behavioral Healthcare. All rights reserved.</div>
    <div class="abs social"></div>
  </div>
</footer>
</body>
</html>
```